Alapca breeding needs a website

Presentation of the farm, animals (stallions, mares, information about the animals, for sale) and possible later expansion with a webshop (alpaca wool products). We want to present our farm and the animals on the farm on this page. A mission why we are doing this. Furthermore, each animal should be shown with a picture and described. Later we want to sell our own products made from alpaca wool via a webshop. But we still need to grow a bit to do that.

Target Market(s)

Information about my alpaca breeding and the alpaca farm

Industry/Entity Type

Tierzucht

Number of Pages Required

1 page

Font styles to use
Sans Serif

Requirements
Must have
• Modern design that matches the logo
Nice to have
• Intuitive operation / Clear structure
Should not have
• No

```html
<!DOCTYPE html>
<html lang="en">
<head>
<meta charset="utf-8">
<title>Sierra Alpacas</title>
<link href="https://fonts.googleapis.com/css2?family=Cinzel:wght@400;500&family=Poppins:wght@400;500;600&display=swap" rel="stylesheet">
<style>
:root{
  --navy:#0c2144;
  --navy-2:#2c4464;
  --green:#7cc242;
  --green-dark:#5a9a2a;
  --cream:#f6f2ec;
  --card:#faf8f5;
  --text:#2a2a2a;
  --muted:#555;
  --white:#fff;
}
*{box-sizing:border-box;margin:0;padding:0}
html,body{width:1200px;height:3824px;overflow:hidden}
body{font-family:"Poppins",sans-serif;color:var(--text);background:var(--cream);position:relative}
.serif{font-family:"Cinzel",serif}
.topbar{height:39px;background:var(--navy);color:var(--white);font-size:13px;font-weight:500;display:flex;align-items:center;justify-content:center}
.header{height:80px;background:var(--cream);position:relative}
.logo{position:absolute;left:111px;top:-39px;width:117px;height:108px;background:var(--white);border-radius:0 0 12px 12px;box-shadow:0 3px 8px rgba(0,0,0,.15);display:flex;flex-direction:column;align-items:center;justify-content:center;gap:6px;z-index:3}
.logo .dot{width:34px;height:34px;border-radius:50%;background:var(--navy)}
.logo .name{font-family:"Poppins",sans-serif;font-weight:600;font-size:13px;color:var(--navy);text-align:center;line-height:1.1}
.search{position:absolute;left:366px;top:17px;width:478px;height:46px;border:1.5px solid var(--navy-2);border-radius:23px;background:var(--white);display:flex;align-items:center;padding:0 4px 0 17px;font-size:13px;color:#aaa;justify-content:space-between}
.search .btn{width:34px;height:34px;border-radius:50%;background:var(--navy);display:flex;align-items:center;justify-content:center}
.divider{position:absolute;left:856px;top:20px;width:2px;height:40px;background:var(--navy-2)}
.socials{position:absolute;left:868px;top:25px;display:flex;gap:10px}
.soc{width:32px;height:32px;border-radius:50%;border:1.5px solid var(--green);display:flex;align-items:center;justify-content:center}
.soc span{width:8px;height:8px;border-radius:50%;background:var(--green)}
.cart{position:absolute;left:1008px;top:22px;display:flex;gap:10px;align-items:center;font-size:11px;color:var(--navy)}
.cart b{display:block;font-size:13px;font-weight:500}
.nav{height:44px;background:var(--green);display:flex;align-items:center;padding-left:145px;gap:0}
.nav a{color:var(--navy);font-size:14px;font-weight:500;text-decoration:none;margin-right:39px}
.nav a.active{background:var(--navy);color:var(--white);padding:6px 14px;border-radius:16px;margin-right:30px}
.hero{height:550px;position:relative;background:linear-gradient(160deg,#e8a850 0%,#b86a2c 35%,#6b4020 70%,#3e2614 100%)}
.hero .alpaca{position:absolute;left:600px;top:30px;width:340px;height:520px;border-radius:160px 160px 40px 40px;background:radial-gradient(ellipse at 50% 40%,#f4efe8,#cfc6b8)}
.hero h1{position:absolute;left:111px;top:165px;font-family:"Cinzel",serif;font-weight:400;font-size:54px;color:var(--white)}
.pill{display:inline-flex;align-items:center;gap:22px;border-radius:24px;font-weight:500;text-transform:uppercase}
.hero .pill{position:absolute;left:113px;top:248px;height:46px;padding:0 20px;background:var(--navy);border:2px solid var(--green);color:var(--white);font-size:13px}
.dots{position:absolute;left:38px;top:200px;display:flex;flex-direction:column;gap:9px}
.dots i{width:14px;height:14px;border-radius:50%;border:1.5px solid #eee;display:block}
.dots i.on{background:var(--green);border-color:var(--green)}
.section{text-align:center;position:relative}
.section h2{font-family:"Cinzel",serif;font-weight:400;font-size:30px;color:var(--navy);padding-top:80px}
.section p.lead{width:920px;margin:22px auto 0;font-size:15px;line-height:25px;color:var(--text)}
.cards{display:flex;gap:14px;width:974px;margin:33px auto 0}
.card{width:233px;height:430px;background:var(--card);border-radius:0 0 8px 8px}
.card .ph{height:266px;border:1px solid var(--green)}
.card h3{font-family:"Cinzel",serif;font-weight:400;font-size:23px;color:#222;margin-top:10px}
.card .sub{font-size:14px;color:var(--muted);margin-top:2px}
.card .price{font-size:28px;font-weight:500;margin-top:8px}
.card .add{margin-top:6px;height:33px;padding:0 14px;border:2px solid var(--green);color:var(--navy);font-size:10px;background:var(--white);gap:6px}
.viewall{margin-top:33px;height:46px;padding:0 22px;background:var(--green);border:2px solid var(--navy);color:var(--white);font-size:13px;gap:36px}
.animals{height:839px}
.mission{height:594px;display:flex}
.mission .ph{width:600px;background:linear-gradient(180deg,#b8cfe0 0%,#d9e2e0 35%,#8fae5f 60%,#6f9440 100%)}
.mission .txt{width:600px;background:var(--navy-2);padding:68px 130px 0 46px;color:var(--white)}
.mission h2{font-family:"Cinzel",serif;font-weight:400;font-size:30px}
.mission .rule{width:132px;height:3px;background:var(--green);margin:14px 0 26px}
.mission p{font-size:15px;line-height:25px}
.mission .pill{margin-top:40px;height:46px;padding:0 20px;background:var(--green);border:2px solid var(--white);color:var(--white);font-size:13px;gap:12px}
.wool{height:999px}
.wool h2{padding-top:75px}
.herd{position:absolute;left:0;bottom:0;width:1200px;height:190px;background:linear-gradient(180deg,rgba(246,242,236,0) 0%,#c08850 35%,#8a5a30 100%)}
.footer{height:620px;background:var(--navy);color:var(--white);text-align:center;position:relative}
.footer h2{font-family:"Cinzel",serif;font-weight:400;font-size:30px;padding-top:70px}
.footer .rule{width:134px;height:3px;background:var(--white);margin:20px auto 0}
.footer h4{font-family:"Cinzel",serif;font-weight:500;font-size:17px;margin-top:45px}
.footer .note{font-size:15px;margin-top:16px}
.sub-form{width:560px;height:42px;margin:26px auto 0;background:var(--white);border:2px solid var(--green);border-radius:22px;display:flex;align-items:center;justify-content:space-between;padding:0 3px 0 16px;font-size:13px;color:#888}
.sub-form .pill{height:34px;padding:0 14px;background:var(--green);border:2px solid var(--navy);color:var(--white);font-size:10px;gap:40px}
.footer .line{position:absolute;left:109px;top:320px;width:978px;height:1px;background:var(--green)}
.foot-brand{position:absolute;left:210px;top:380px;width:148px;text-align:center}
.foot-brand .dot{width:48px;height:48px;border-radius:50%;background:var(--white);margin:0 auto 10px}
.foot-brand .name{font-weight:600;font-size:24px;line-height:1.05}
.foot-soc{position:absolute;left:208px;top:536px;display:flex;gap:13px}
.foot-soc .soc{width:40px;height:40px;background:var(--green);border:2px solid var(--white)}
.foot-soc .soc span{background:var(--white)}
.col{position:absolute;top:378px;text-align:left}
.col h5{font-family:"Cinzel",serif;font-weight:500;font-size:17px}
.col .rule{width:50px;height:2px;background:var(--green);margin:12px 0 16px}
.col a{display:block;color:var(--white);font-size:13px;text-decoration:none;line-height:26px}
.copy{height:59px;background:var(--green);color:var(--navy);font-size:12px;display:flex;align-items:center;justify-content:center}
</style>
</head>
<body>
<div class="topbar">Free shipping on orders over US$100!</div>
<header class="header">
  <div class="logo"><span class="dot"></span><span class="name">SIERRA<br>ALPACAS</span></div>
  <div class="search">Search<span class="btn"><svg width="16" height="16" viewBox="0 0 16 16" fill="none" stroke="#fff" stroke-width="2"><circle cx="7" cy="7" r="5"/><path d="M11 11l4 4"/></svg></span></div>
  <div class="divider"></div>
  <div class="socials"><span class="soc"><span></span></span><span class="soc"><span></span></span><span class="soc"><span></span></span></div>
  <div class="cart"><svg width="22" height="28" viewBox="0 0 22 28"><path d="M6 9V6a5 5 0 0110 0v3" fill="none" stroke="#0c2144" stroke-width="2"/><rect x="1" y="9" width="20" height="18" rx="3" fill="#0c2144"/></svg><div><b>(2)</b>MY CART</div></div>
</header>
<nav class="nav"><a class="active">Home</a><a>About Us</a><a>Our Animals</a><a>Mission</a><a>Alpacas Wool</a><a>Testimonials</a><a>Blogs</a><a>FAQ's</a><a>Contact Us</a></nav>
<section class="hero" role="img" aria-label="White alpaca standing on grassy hills at sunset">
  <div class="alpaca"></div>
  <div class="dots"><i></i><i class="on"></i><i></i><i></i></div>
  <h1>SIERRA ALPACAS</h1>
  <span class="pill">Shop Now <svg width="8" height="10" viewBox="0 0 8 10" fill="none" stroke="#fff" stroke-width="1.6"><path d="M2 1l4 4-4 4"/></svg></span>
</section>
<section class="section animals">
  <h2>OUR ANIMALS</h2>
  <p class="lead">Kaicaessa piciatis unde omnis iste natus error sit voluptatem accusantium doloremque laudantium, totam rem aperiam, eaque ipsa quae ab illo inventore veritatis et quasi architecto beatae vitae dicta sunt explicabo. Nemo enim ipsam voluptatem quia voluptas sit aspernatur</p>
  <div class="cards">
    <div class="card"><div class="ph" role="img" aria-label="Dark brown stallion on a gravel path" style="background:linear-gradient(180deg,#cfd6cf,#7a5540 60%,#d8d2c8)"></div><h3>STALLIONS</h3><div class="sub">Casei asemcas eqsesa</div><div class="price">$50.00</div><span class="pill add">Add to Cart ›</span></div>
    <div class="card"><div class="ph" role="img" aria-label="Cream mare on a hillside" style="background:linear-gradient(180deg,#b8a484,#d9c6a0 50%,#6e5a3a)"></div><h3>MARES</h3><div class="sub">Casei asemcas eqsesa</div><div class="price">$50.00</div><span class="pill add">Add to Cart ›</span></div>
    <div class="card"><div class="ph" role="img" aria-label="Pale horse in misty golden light" style="background:linear-gradient(180deg,#a88a60,#c8b898 50%,#5a4a30)"></div><h3>BRONCO</h3><div class="sub">Casei asemcas eqsesa</div><div class="price">$50.00</div><span class="pill add">Add to Cart ›</span></div>
    <div class="card"><div class="ph" role="img" aria-label="Bay horse in a green meadow" style="background:linear-gradient(180deg,#d9e0e4,#8a5a30 50%,#8aa560)"></div><h3>CLYDESDALE</h3><div class="sub">Casei asemcas eqsesa</div><div class="price">$50.00</div><span class="pill add">Add to Cart ›</span></div>
  </div>
  <span class="pill viewall">View All <span>›</span></span>
</section>
<section class="mission">
  <div class="ph" role="img" aria-label="Fluffy white alpaca in a green field"></div>
  <div class="txt">
    <h2>OUR MISSION</h2>
    <div class="rule"></div>
    <p>Paerses asejsepiciatis unde omnis iste natus error drrsit voluptatem accusantium dolor drdremque laudantium, totam rem aperiam, eaque ipsa quae abdr illo inventore veritatis drdrret quasi architecto beatae vitae dicta sunt explicabo. Nemo enim ipsam voluptatem quia voluptas sit aspernatur aut odit aut fugit, sed quia consequuntur magni dolores edros dsrdrqui ratione voluptatem sequi nesciunt. Neque porro quisquam est, qui dolorem ipsum quia dolor sit amet, consectetur, adipisci velit, sed quia non numquam eius modi tempora incidunt ut labore et dolore magnam aliquam.</p>
    <span class="pill">Learn More ›</span>
  </div>
</section>
<section class="section wool">
  <h2>ALPACAS WOOL</h2>
  <p class="lead">Kaicaessa piciatis unde omnis iste natus error sit voluptatem accusantium doloremque laudantium, totam rem aperiam, eaque ipsa quae ab illo inventore veritatis et quasi architecto beatae vitae dicta sunt explicabo. Nemo enim ipsam voluptatem quia voluptas sit aspernatur</p>
  <div class="cards">
    <div class="card"><div class="ph" role="img" aria-label="Raw wool with a drop spindle in a basket" style="background:linear-gradient(160deg,#d8cfc2,#f1ece4 50%,#8a6a48)"></div><h3>CASEP SAESCA</h3><div class="sub">Casei asemcas eqsesa</div><div class="price">$50.00</div><span class="pill add">Add to Cart ›</span></div>
    <div class="card"><div class="ph" role="img" aria-label="Close-up of curly alpaca fleece" style="background:linear-gradient(160deg,#e4dccd,#cbbfa8)"></div><h3>CASEP SAESCA</h3><div class="sub">Casei asemcas eqsesa</div><div class="price">$50.00</div><span class="pill add">Add to Cart ›</span></div>
    <div class="card"><div class="ph" role="img" aria-label="Baskets of white wool rovings" style="background:linear-gradient(180deg,#4a4038,#efeae2 40%,#b07c44 60%,#e8e2d8)"></div><h3>CASEP SAESCA</h3><div class="sub">Casei asemcas eqsesa</div><div class="price">$50.00</div><span class="pill add">Add to Cart ›</span></div>
    <div class="card"><div class="ph" role="img" aria-label="Yarn balls in a woven basket" style="background:linear-gradient(180deg,#8c8270,#e2dccf 45%,#8a5a34)"></div><h3>CASEP SAESCA</h3><div class="sub">Casei asemcas eqsesa</div><div class="price">$50.00</div><span class="pill add">Add to Cart ›</span></div>
  </div>
  <span class="pill viewall">View All <span>›</span></span>
  <div class="herd" role="img" aria-label="Row of alpacas in brown, cream and spotted coats"></div>
</section>
<footer class="footer">
  <h2>STAY CONNECTED WITH US</h2>
  <div class="rule"></div>
  <h4>SIGN UP FOR OUR NEWSLETTER</h4>
  <p class="note">Be the first to know about new arrivals, exclusive offers, and the latest from Us.</p>
  <div class="sub-form">Email<span class="pill">Submit <span>›</span></span></div>
  <div class="line"></div>
  <div class="foot-brand"><div class="dot"></div><div class="name">SIERRA<br>ALPACAS</div></div>
  <div class="foot-soc"><span class="soc"><span></span></span><span class="soc"><span></span></span><span class="soc"><span></span></span></div>
  <div class="col" style="left:503px"><h5>QUICK LINKS</h5><div class="rule"></div><a>Home</a><a>About Us</a><a>Our Animals</a><a>Mission</a><a>Alpacas Wool</a><a>Testimonials</a></div>
  <div class="col" style="left:709px"><h5>LINKS</h5><div class="rule"></div><a>Copyright</a><a>Terms of Use</a><a>Privacy Policy</a><a>Accessibility</a><a>Sitemap</a><a>Blogs</a></div>
  <div class="col" style="left:893px"><h5>SUPPORT</h5><div class="rule"></div><a>Team</a><a>About Us</a><a>Careers</a><a>Our Values</a><a>Online Store</a></div>
</footer>
<div class="copy">© Copyright 2024. All Rights Reserved.</div>
</body>
</html>
```